Business Card Design

New business card design

Target Market(s)

Residential & Commercial Property Managers

Industry/Entity Type

Plumbing Services

Contact Information for Business Card

Name - Rowan Keddle, title - Director, Phone Number - 0431 286 517, email - rowan@tbk-plumbing.com.au, Company ABN - 73 215 904 386,

Font styles to use
Sans Serif

Colors
0054AA
0677BA
7BADD7
CADEEF
E8F1F8

```html
<!DOCTYPE html>
<html lang="en">
<head>
<meta charset="utf-8">
<title>TBK Plumbing Services – Business Card</title>
<link href="https://fonts.googleapis.com/css2?family=Montserrat:wght@400;500;700&display=swap" rel="stylesheet">
<style>
  :root {
    --page-bg: #e9ecef;
    --card-bg: #ffffff;
    --ink: #1c2530;
    --ink-soft: #2b2f36;
    --accent: #29a8e0;
    --white: #ffffff;
  }
  * { box-sizing: border-box; margin: 0; padding: 0; }
  html, body { width: 1200px; height: 900px; overflow: hidden; }
  body {
    background: var(--page-bg);
    font-family: "Montserrat", sans-serif;
    display: flex;
    align-items: center;
    justify-content: center;
    gap: 36px;
  }
  .card {
    position: relative;
    width: 560px;
    height: 320px;
    background: var(--card-bg);
    border-radius: 30px;
    overflow: hidden;
    box-shadow: 0 10px 28px rgba(0,0,0,0.18);
  }

  /* Brand lockup */
  .brand { color: var(--ink); font-weight: 500; line-height: 1; }
  .brand-name { display: block; letter-spacing: 0.04em; }
  .brand-tagline { display: block; letter-spacing: 0.55em; text-transform: lowercase; }

  /* Back side */
  .card-back .brand {
    position: absolute;
    left: 0; right: 0; top: 90px;
    text-align: center;
  }
  .card-back .brand-name { font-size: 96px; text-transform: lowercase; }
  .card-back .brand-tagline { font-size: 15px; margin-top: 18px; padding-left: 0.55em; }

  /* Front side */
  .card-front .brand {
    position: absolute;
    left: 30px; top: 96px;
    width: 220px;
    text-align: center;
  }
  .card-front .brand-name { font-size: 58px; text-transform: lowercase; }
  .card-front .brand-tagline { font-size: 9px; margin-top: 14px; letter-spacing: 0.5em; padding-left: 0.5em; }

  .divider {
    position: absolute;
    left: 276px; top: 70px;
    width: 1.5px; height: 170px;
    background: var(--accent);
  }
  .contact {
    position: absolute;
    left: 298px; top: 92px;
  }
  .contact-name { color: var(--accent); font-weight: 700; font-size: 23px; letter-spacing: 0.01em; }
  .contact-title { color: var(--ink-soft); font-weight: 500; font-size: 14px; margin-top: 2px; }
  .contact-list { list-style: none; margin-top: 22px; }
  .contact-list li {
    display: flex; align-items: center; gap: 8px;
    color: var(--ink-soft); font-size: 14px; margin-bottom: 6px;
  }
  .contact-list svg { width: 14px; height: 14px; flex: none; }

  .abn-band {
    position: absolute;
    left: 0; right: 0; top: 264px;
    height: 22px;
    background: var(--accent);
    color: var(--white);
    font-size: 13px;
    font-weight: 400;
    display: flex; align-items: center;
    padding-left: 150px;
    letter-spacing: 0.02em;
  }
  .band-dot {
    position: absolute;
    right: 48px; top: 256px;
    width: 38px; height: 38px;
    border-radius: 50%;
    background: var(--accent);
    border: 3px solid var(--white);
  }
</style>
</head>
<body>

  <section class="card card-back" aria-label="Business card back">
    <div class="brand">
      <span class="brand-name">tbk</span>
      <span class="brand-tagline">plumbing services</span>
    </div>
  </section>

  <section class="card card-front" aria-label="Business card front">
    <div class="brand">
      <span class="brand-name">tbk</span>
      <span class="brand-tagline">plumbing services</span>
    </div>

    <div class="divider"></div>

    <div class="contact">
      <p class="contact-name">Rowan Keddle</p>
      <p class="contact-title">Director</p>
      <ul class="contact-list">
        <li>
          <svg viewBox="0 0 24 24" aria-hidden="true"><path fill="#29a8e0" d="M6.6 10.8a15.1 15.1 0 0 0 6.6 6.6l2.2-2.2a1 1 0 0 1 1-.25 11.4 11.4 0 0 0 3.6.57 1 1 0 0 1 1 1V20a1 1 0 0 1-1 1A17 17 0 0 1 3 4a1 1 0 0 1 1-1h3.5a1 1 0 0 1 1 1c0 1.25.2 2.45.57 3.57a1 1 0 0 1-.25 1z"/></svg>
          0431 286 517
        </li>
        <li>
          <svg viewBox="0 0 24 24" aria-hidden="true"><rect x="2" y="5" width="20" height="14" rx="2" fill="none" stroke="#29a8e0" stroke-width="2"/><path d="M3 6l9 7 9-7" fill="none" stroke="#29a8e0" stroke-width="2"/></svg>
          rowan@tbk-plumbing.com.au
        </li>
      </ul>
    </div>

    <div class="abn-band">Company ABN - 73 215 904 386</div>
    <div class="band-dot" aria-hidden="true"></div>
  </section>

</body>
</html>
```